Creating a website for a life changing company (Halvra Q)

We do need a website for our Coaching and Consulting business we recently launched. We do need it for information purposes and that our clients do have the opportunity to subscribe for packages, programs etc.
We would like to see designs which use the colours blue and yellow (see attachment). The final design should communicate our passion for the potential in people and the benefit (rising onward) for them.
Updates
Additional information:
Our company (webpage): Halvra Q (the C stands for "what people cannot see / imagine now...)
Welcome to Halvra Q(uarry)
Consulting (O.R.T.) & Coaching (Rise onward)
Two pillars:
1) O.R.T. ( Steward pathway - Our program - focussing on companies - business orientated)
2) Rise onward (Daily renewal - Events - focusing on individuals - primarily life changing)
For both of them we offer: Lanternhall & Halvra Q+ (This should go as a subscription)
Eventually you can draft this as a rhombus
Industry/Entity Type
Coaching / Consulting
Coding
Coded - Design and coding required
Number of Pages Required
1 page
Font styles to use
Other font styles liked:
- Lato
Requirements
Must have
- Please see attachment (About us / Offers / Calendar function / Links to Snapfeed and LinkedIn account / mailing list / page for clients
Nice to have
- A banner

```html
<!DOCTYPE html>
<html lang="en">
<head>
<meta charset="utf-8">
<title>Halvra Q — Coaching &amp; Consulting</title>
<link href="https://fonts.googleapis.com/css2?family=Poppins:wght@400;500;600;700;800&display=swap" rel="stylesheet">
<style>
:root{
  --blue:#1d4f9b;
  --blue-bright:#1b5fc4;
  --navy:#173a74;
  --yellow:#f6d22e;
  --pale:#e4eaf2;
  --ink:#333a45;
  --white:#ffffff;
  --black:#000000;
}
*{margin:0;padding:0;box-sizing:border-box}
html,body{width:1200px;height:5106px;overflow:hidden}
body{font-family:'Poppins',sans-serif;color:var(--ink);background:var(--white);position:relative}
.abs{position:absolute}
a{color:inherit;text-decoration:none}

/* header */
.hero{left:0;top:0;width:1200px;height:714px;background:linear-gradient(120deg,#2f4a26 0%,#5d6f4a 35%,#8a8a7a 55%,#c9b89a 75%,#6d6b5c 100%)}
.hero-shade{left:0;top:0;width:700px;height:714px;background:linear-gradient(90deg,rgba(0,0,0,.35),rgba(0,0,0,0))}
.topbar{left:0;top:0;width:1200px;height:104px}
.topbar .contact{top:12px;font-size:15px;color:#222;display:flex;align-items:center;gap:8px}
.social{top:12px;left:928px;display:flex;gap:22px}
.social span{width:26px;height:26px;border-radius:50%;background:var(--blue-bright);display:block}
.nav{top:68px;left:407px;display:flex;gap:30px;font-size:15px;color:var(--white)}
.brand{left:110px;top:34px;display:flex;align-items:center;gap:16px;color:var(--white);font-weight:600;font-size:18px;letter-spacing:4px}
.brand i{display:block;width:24px;height:2px;background:var(--white)}
.hero-title{left:109px;top:214px;color:var(--white);font-size:56px;font-weight:800;line-height:62px;letter-spacing:.5px}
.hero-text{left:109px;top:350px;width:300px;color:var(--white);font-size:15px;line-height:24px}
.btn{display:inline-flex;align-items:center;justify-content:center;background:var(--blue-bright);color:var(--white);font-weight:600;font-size:15px;border-radius:24px}
.hero-btn{left:109px;top:440px;width:218px;height:42px}

/* section heading */
.heading{left:0;width:1200px;text-align:center;color:var(--blue);font-weight:700;font-size:36px;display:flex;justify-content:center;align-items:center;gap:16px}
.heading::before,.heading::after{content:"";width:74px;height:3px;background:var(--blue)}
.lead{left:170px;width:860px;text-align:center;font-size:15px;line-height:26px}

/* O.R.T cards */
.pillar{top:930px;width:290px;height:337px;border-radius:14px;overflow:hidden;color:var(--white)}
.pillar h3{position:absolute;left:0;right:0;bottom:38px;text-align:center;font-size:24px;font-weight:600}
.pillar.active{background:linear-gradient(160deg,#e4d41a,#b2b01a 60%,#6f6d12);border-radius:14px;color:#222;text-align:center;padding:60px 28px 0;box-shadow:4px 4px 0 #4b4a35}
.pillar.active h3{position:static;font-size:24px;margin-bottom:12px;color:#111}
.pillar.active p{font-size:14px;line-height:24px}
.pillar.active a{display:inline-block;margin-top:10px;font-weight:700;font-size:15px;border-bottom:2px solid #222}

/* about */
.about-bg{left:321px;top:1352px;width:557px;height:460px;background:var(--pale)}
.about-photo{top:1352px;height:460px}
.about-head{left:321px;top:1400px;width:557px;font-size:30px}
.about-head::before,.about-head::after{width:70px}
.about-text{left:405px;top:1458px;width:395px;font-size:15px;line-height:26px;text-align:justify}
.about-btn{left:405px;top:1727px;width:133px;height:44px}

/* lanternhall cards */
.svc{width:310px}
.svc-back{background:#d7e1ee;border-radius:6px}
.svc-photo{left:0;top:0;width:310px;height:182px}
.svc-box{left:14px;top:182px;width:282px;height:232px;background:var(--white);box-shadow:0 4px 14px rgba(0,0,0,.08);text-align:center;padding:30px 22px 0}
.svc-box h4{color:var(--blue);font-size:20px;font-weight:600;margin-bottom:12px}
.svc-box p{font-size:13.5px;line-height:23px}
.svc-box a{display:inline-block;margin-top:4px;color:var(--blue);font-weight:700;font-size:15px;border-bottom:2px solid var(--blue)}

/* programs */
.programs-bg{left:0;top:2604px;width:1200px;height:168px;background:var(--pale)}
.tile{width:600px;height:354px}
.tile h5{position:absolute;left:41px;top:260px;color:var(--white);font-size:22px;font-weight:500}
.tile a{position:absolute;left:41px;top:300px;color:var(--white);font-size:14px;border-bottom:1.5px solid var(--white)}

/* packages */
.pack-bg{left:0;top:3480px;width:1200px;height:960px;background:#edf1f7}
.toggle{left:405px;top:3668px;width:386px;height:50px;display:flex;font-weight:700;font-size:14px}
.toggle span{flex:1;display:flex;align-items:center;justify-content:center;border:2px solid var(--yellow)}
.toggle .on{background:var(--yellow)}
.toggle .off{background:var(--white)}
.badge{left:520px;top:3758px;width:158px;height:46px;background:var(--navy);color:var(--white);font-weight:600;font-size:14px;display:flex;align-items:center;justify-content:center;border-radius:3px 3px 0 0}
.plan{top:3802px;width:306px;background:var(--white);border-radius:12px;text-align:center;box-shadow:0 4px 18px rgba(0,0,0,.05)}
.plan h6{margin-top:38px;font-size:22px;font-weight:400;color:#222}
.plan.ultra h6{font-weight:700}
.plan .price{font-size:26px;color:var(--yellow);font-weight:500;margin-top:6px}
.plan ul{list-style:none;text-align:left;margin:14px 0 0 72px}
.plan li{font-size:14px;line-height:32px;display:flex;align-items:center;gap:12px}
.plan li::before{content:"";width:10px;height:10px;border-radius:50%;background:var(--yellow)}
.plan .choose{margin-top:18px;width:148px;height:42px;background:var(--navy);font-size:14px}
.plan.ultra{border:3px solid var(--navy);height:446px}
.plan.ultra .choose{position:absolute;left:76px;bottom:-22px}

/* footer */
.footer{left:0;top:4383px;width:1200px;height:723px;background:var(--black);color:var(--white)}
.signup{left:0;top:4553px;width:1200px;text-align:center;font-size:30px;font-weight:600}
.signup-sub{left:0;top:4604px;width:1200px;text-align:center;font-size:15px}
.mail-form{left:244px;top:4644px;width:710px;height:48px;background:var(--white);border-radius:26px;display:flex;align-items:center;justify-content:space-between;padding:0 4px 0 24px;color:#333;font-size:15px}
.mail-form .btn{height:40px;width:108px;font-size:14px;background:var(--navy)}
.rule{left:111px;top:4733px;width:976px;height:1px;background:#444}
.foot-brand{left:110px;top:4822px;display:flex;align-items:center;gap:18px;font-weight:600;font-size:20px;letter-spacing:5px}
.foot-brand i{display:block;width:30px;height:2px;background:var(--white)}
.col{top:4772px;font-size:14px}
.col h6{font-size:19px;font-weight:500;margin-bottom:8px}
.col li{list-style:none;line-height:32px}
.follow li{display:flex;align-items:center;gap:12px;line-height:45px}
.follow li::before{content:"";width:30px;height:30px;border-radius:50%;border:2px solid var(--white)}
.copy{left:0;top:5056px;width:1200px;text-align:center;font-size:14px}
</style>
</head>
<body>

<!-- HERO -->
<div class="abs hero" role="img" aria-label="Woman meditating in a yoga pose on a wooden deck before a forest waterfall"></div>
<div class="abs hero-shade"></div>

<svg class="abs" style="left:0;top:0" width="1200" height="104" viewBox="0 0 1200 104" aria-hidden="true">
  <polygon points="340,0 1200,0 1200,54 380,54" fill="#ffffff"/>
  <polygon points="380,54 1200,54 1200,104 420,104" fill="#1b5fc4"/>
</svg>

<div class="abs brand"><i></i>HALVRA Q<i></i></div>

<div class="abs contact topbar" style="height:auto">
  <div class="abs contact" style="left:436px">
    <svg width="16" height="16" viewBox="0 0 24 24" aria-hidden="true"><rect width="24" height="24" rx="4" fill="#1d4f9b"/><path d="M8 5l2 4-2 1.5a10 10 0 0 0 5.5 5.5L15 14l4 2-1 3c-7 0-13-6-13-13z" fill="#fff"/></svg>
    <span>| +1 555 204 318</span>
  </div>
  <div class="abs contact" style="left:650px">
    <svg width="18" height="14" viewBox="0 0 24 18" aria-hidden="true"><rect width="24" height="18" rx="2" fill="#1d4f9b"/><path d="M2 3l10 7 10-7" stroke="#fff" stroke-width="2" fill="none"/></svg>
    <span>| hello@halvraq.example</span>
  </div>
  <div class="abs social"><span></span><span></span><span></span><span></span></div>
</div>

<nav class="abs nav">
  <a>Home</a><a>About Us</a><a>O.R.T</a><a>Lanternhall</a><a>Rise Onward</a><a>Halvra Q +</a><a>Testimonials</a>
</nav>

<h1 class="abs hero-title">WELCOME TO<br>HALVRA Q</h1>
<p class="abs hero-text">Lorem ipsum dolor sit amet, consectetur adipiscing elit, sed do eiusmod tempor incididunt ut aliqua.</p>
<a class="abs btn hero-btn">Book An Appointment</a>

<svg class="abs" style="left:0;top:560px" width="1200" height="156" viewBox="0 0 1200 156" preserveAspectRatio="none" aria-hidden="true">
  <path d="M0 150 C250 70 520 10 800 40 C980 60 1100 100 1200 120 L1200 156 L0 156Z" fill="#f6d22e"/>
  <path d="M0 156 C260 95 520 45 800 70 C980 86 1100 120 1200 146 L1200 156Z" fill="#ffffff"/>
</svg>

<!-- O.R.T -->
<h2 class="abs heading" style="top:786px">O.R.T</h2>
<p class="abs lead" style="top:842px">Lorem ipsum dolor sit amet, consectetur adipiscing elit, sed do eiusmod tempor incididunt ut labore et dolore magna aliqua.</p>

<div class="abs pillar" style="left:111px;background:linear-gradient(180deg,#4a6f8e 0%,#b3683a 45%,#3d4a2c 100%)" role="img" aria-label="Tiered temple tower on a lake under a cloudy sunset sky">
  <h3>Architecure</h3>
</div>
<div class="abs pillar active" style="left:454px">
  <h3>Courage</h3>
  <p>Lorem ipsum dolor sit amet, consectetur adipiscing elit, sed do eiusmod tempor incididunt ut labore et dolore magna aliqua. commodo consequat.</p>
  <a>Raed More</a>
</div>
<div class="abs pillar" style="left:797px;background:linear-gradient(180deg,#cfd3de 0%,#a48fb0 50%,#5d4676 100%)" role="img" aria-label="Glass distillation still in front of a lavender field">
  <h3>Essentials</h3>
</div>

<!-- ABOUT -->
<div class="abs about-photo" style="left:0;width:321px;background:linear-gradient(160deg,#c9ccd2,#2b4173 55%,#1c2c55)" role="img" aria-label="Portrait of the founder in a blue suit"></div>
<div class="abs about-bg"></div>
<div class="abs about-photo" style="left:878px;width:322px;background:linear-gradient(160deg,#1f2838,#2c3446 60%,#1a2130)" role="img" aria-label="Dimly lit portrait of a client"></div>
<h2 class="abs heading about-head">ABOUT EDVIN</h2>
<p class="abs about-text">Lorem ipsum dolor sit amet, consectetur adipiscing elit, sed do eiusmod tempor incididunt ut labore et dolore magna aliqua. Ut enim ad minim veniam, quis nostrud exercitation ullamco laboris nisi ut aliquip ex ea commodo consequat.Lorem ipsum dolor sit amet, consectetur adipiscing elit, sed do eiusmod tempor incididunt ut labore et dolore magna aliqua. Ut enim ad minim veniam, quis nostrud exercitation ullamco laboris nisi ut aliquip ex ea commodo consequat.</p>
<a class="abs btn about-btn">Read More</a>

<!-- LANTERNHALL -->
<h2 class="abs heading" style="top:1888px">LANTERNHALL</h2>
<p class="abs lead" style="top:1942px">Lorem ipsum dolor sit amet, consectetur adipiscing elit, sed do eiusmod tempor incididunt ut labore et dolore magna aliqua.</p>

<div class="abs svc svc-back" style="left:111px;top:2029px;height:430px">
  <div class="abs svc-photo" style="background:linear-gradient(160deg,#e8e8e8,#9b9fa6 50%,#3c3f45)" role="img" aria-label="Coach guiding a client on an exercise ball in a gym"></div>
  <div class="abs svc-box"><h4>Coaching</h4><p>Lorem ipsum dolor sit amet, consectetur adipiscing elit, sed do eiusmod tempor incididunt ut labore et dolore magna aliqua. Ut enim ad minim veniam.</p><a>Raed More</a></div>
</div>
<div class="abs svc svc-back" style="left:444px;top:2088px;height:430px">
  <div class="abs svc-photo" style="background:linear-gradient(160deg,#dfe6ea,#9fb0b5 50%,#5a6b70)" role="img" aria-label="Smiling consultant in conversation at a bright office table"></div>
  <div class="abs svc-box"><h4>Consulting</h4><p>Lorem ipsum dolor sit amet, consectetur adipiscing elit, sed do eiusmod tempor incididunt ut labore et dolore magna aliqua. Ut enim ad minim veniam.</p><a>Raed More</a></div>
</div>
<div class="abs svc svc-back" style="left:776px;top:2029px;height:430px">
  <div class="abs svc-photo" style="background:linear-gradient(160deg,#3a2c24,#8b6a55 50%,#c9b39e)" role="img" aria-label="Two people talking closely in a warm room"></div>
  <div class="abs svc-box"><h4>Fireside Chat</h4><p>Lorem ipsum dolor sit amet, consectetur adipiscing elit, sed do eiusmod tempor incididunt ut labore et dolore magna aliqua. Ut enim ad minim veniam.</p><a>Raed More</a></div>
</div>

<!-- PROGRAMS -->
<div class="abs programs-bg"></div>
<h2 class="abs heading" style="top:2664px">PROGRAMS</h2>
<div class="abs tile" style="left:0;top:2772px;background:linear-gradient(180deg,#8a7a63 0%,#e0a93a 45%,#5c4a25 100%)" role="img" aria-label="Sun rising over misty mountain ridges and a forest">
  <h5>Lorem Ipsum Dolor Sit</h5><a>Learn More</a></div>
<div class="abs tile" style="left:600px;top:2772px;background:linear-gradient(180deg,#4a5a76 0%,#d89a62 40%,#40506a 60%,#6d655c 100%)" role="img" aria-label="Wooden boardwalk leading to the sea at sunset with birds in flight">
  <h5>Lorem ipsum dolor sit</h5><a>Learn More</a></div>
<div class="abs tile" style="left:0;top:3126px;background:linear-gradient(180deg,#8a7f6a 0%,#55575a 45%,#24262a 100%)" role="img" aria-label="Stacked balancing stones on a pebble beach">
  <h5>Lorem ipsum dolor sit</h5><a>Learn More</a></div>
<div class="abs tile" style="left:600px;top:3126px;background:linear-gradient(140deg,#9fb36a 0%,#3e4a45 40%,#27303d 100%)" role="img" aria-label="Older woman with headphones at a laptop by a window">
  <h5>Lorem ipsum dolor sit</h5><a>Learn More</a></div>

<!-- PACKAGES -->
<div class="abs pack-bg"></div>
<h2 class="abs heading" style="top:3584px">SUBSCRIBE FOR PACKAGES</h2>
<div class="abs toggle"><span class="off">ONE TIME ACCESS</span><span class="on">MONTH ACCESS</span></div>
<div class="abs badge">Best Value</div>

<div class="abs plan" style="left:111px;height:366px">
  <h6>Basic</h6><div class="price">$ 50/Mo*</div>
  <ul><li>Lorem ipsum dolor</li><li>Lorem ipsum dolor</li><li>Lorem ipsum dolor</li><li>Lorem ipsum dolor</li></ul>
  <a class="btn choose">Choose Plan</a>
</div>
<div class="abs plan ultra" style="left:444px">
  <h6>Ultra</h6><div class="price">$ 170 /Mo *</div>
  <ul><li>Lorem ipsum dolor</li><li>Lorem ipsum dolor</li><li>Lorem ipsum dolor</li><li>Lorem ipsum dolor</li><li>Lorem ipsum dolor</li><li>Lorem ipsum dolor</li><li>Lorem ipsum dolor</li><li>Lorem ipsum dolor</li></ul>
  <a class="btn choose">Choose Plan</a>
</div>
<div class="abs plan" style="left:781px;height:366px">
  <h6>Premium</h6><div class="price">$ 90/Mo*</div>
  <ul><li>Lorem ipsum dolor</li><li>Lorem ipsum dolor</li><li>Lorem ipsum dolor</li><li>Lorem ipsum dolor</li></ul>
  <a class="btn choose">Choose Plan</a>
</div>

<!-- FOOTER -->
<div class="abs footer"></div>
<svg class="abs" style="left:0;top:4330px" width="1200" height="110" viewBox="0 0 1200 110" preserveAspectRatio="none" aria-hidden="true">
  <path d="M0 0 L1200 0 L1200 40 C1000 10 800 0 560 20 C360 38 160 70 0 90Z" fill="#edf1f7"/>
  <path d="M0 90 C160 70 360 38 560 20 C800 0 1000 10 1200 40 L1200 70 C1000 40 800 32 560 50 C360 66 160 95 0 110Z" fill="#f6d22e"/>
</svg>

<svg class="abs" style="left:578px;top:4490px" width="46" height="40" viewBox="0 0 46 40" aria-hidden="true">
  <path d="M4 14 L4 36 L38 36 L38 14 M4 14 L21 26 L38 14 M4 14 L21 4 L28 8" stroke="#fff" stroke-width="2.5" fill="none" stroke-linejoin="round"/>
  <circle cx="36" cy="9" r="7" stroke="#fff" stroke-width="2.5" fill="#000"/>
</svg>
<h2 class="abs signup">SIGN UP FOR HALVRA Q</h2>
<p class="abs signup-sub">Arrange a live demo today!</p>
<div class="abs mail-form"><span>Enter Email Address</span><a class="btn">SUBMIT</a></div>
<div class="abs rule"></div>

<div class="abs foot-brand" style="color:#fff"><i></i>HALVRA Q<i></i></div>

<div class="abs col" style="left:520px;color:#fff">
  <h6>USE LINK</h6>
  <ul><li>Home</li><li>About Us</li><li>O.R.T</li><li>Lanternhall</li><li>Rise Onward</li><li>Halvra Q +</li><li>Testimonials</li></ul>
</div>
<div class="abs col" style="left:720px;color:#fff">
  <h6>HELP LINK</h6>
  <ul><li>Terms &amp; Conditions</li><li>Privacy Policy</li><li>Support</li><li>Our Location</li></ul>
</div>
<div class="abs col follow" style="left:946px;color:#fff">
  <h6>FOLLOW US</h6>
  <ul><li>Friendwall</li><li>Linkwork</li><li>Snapfeed</li><li>Chirpline</li></ul>
</div>

<p class="abs copy" style="color:#fff">Copyrights © 2022 Halvra Q | All Rights Reserved.</p>

</body>
</html>
```